SkyvornQ Business Cards and Stationary Design

Need a design for our business cards and stationary. I want to carry on the theme of the logo. I want the business cards to have a design on the back. I would like the business cards and the stationary to carry the same theme, design scheme, and branding

Target Market(s)

Airlines and Maintenance Facilities

Industry/Entity Type

Aviation

Contact Information for Business Card

Name
Position Title
Address: 4827 Trellis Hollow Road, Fort Pierce, Florida, 34951
Office Number
Mobile Number
Email
Website

Font styles to use
Serif
Sans Serif

Colors

Designer to choose colors to be used in the design.

```html
<!DOCTYPE html>
<html lang="en">
<head>
<meta charset="UTF-8">
<title>SkyvornQ Business Card</title>
<link href="https://fonts.googleapis.com/css2?family=Montserrat:wght@400;500;700;800&display=swap" rel="stylesheet">
<style>
  :root {
    --stage: #1d1e20;
    --card-white: #ffffff;
    --card-shade: #eef0f2;
    --navy: #1b3a78;
    --sky: #2f9fd8;
    --sky-deep: #1f86c2;
    --sky-light: #3cb0e6;
    --ink: #3a3d42;
    --muted: #6b6f76;
    --pale: #e8eef2;
  }
  * { box-sizing: border-box; margin: 0; padding: 0; }
  html, body { width: 1200px; height: 800px; overflow: hidden; }
  body {
    background: var(--stage);
    font-family: "Montserrat", sans-serif;
    position: relative;
  }
  .card {
    position: absolute;
    top: 250px;
    width: 525px;
    height: 300px;
    border-radius: 16px;
    overflow: hidden;
  }
  .card-front {
    left: 50px;
    background: linear-gradient(135deg, var(--card-white) 0%, var(--card-shade) 100%);
  }
  .card-back { left: 625px; }

  .front-brand {
    position: absolute;
    left: 34px;
    top: 70px;
    width: 210px;
    display: flex;
    flex-direction: column;
    align-items: flex-end;
    gap: 10px;
  }
  .front-brand .brand-dot {
    width: 40px; height: 40px;
    border-radius: 50%;
    background: var(--navy);
    margin-right: 40px;
  }
  .front-brand .brand-name {
    font-weight: 800;
    font-size: 25px;
    letter-spacing: 3px;
    text-transform: uppercase;
    color: var(--navy);
    white-space: nowrap;
  }
  .divider {
    position: absolute;
    left: 268px;
    top: 78px;
    width: 1px;
    height: 120px;
    background: var(--sky);
  }
  .contact {
    position: absolute;
    left: 286px;
    top: 80px;
    width: 225px;
  }
  .person-name {
    font-weight: 700;
    font-size: 17px;
    letter-spacing: 1px;
    text-transform: uppercase;
    color: var(--sky);
    white-space: nowrap;
  }
  .person-title {
    font-size: 11px;
    color: var(--muted);
    margin-top: 3px;
    margin-bottom: 10px;
  }
  .contact-list { list-style: none; }
  .contact-list li {
    display: flex;
    align-items: center;
    gap: 8px;
    font-size: 11.5px;
    color: var(--ink);
    line-height: 20px;
    white-space: nowrap;
  }
  .contact-list svg { width: 11px; height: 11px; flex: none; }
  .address {
    position: absolute;
    left: 34px;
    bottom: 34px;
    font-size: 11.5px;
    color: var(--ink);
    letter-spacing: 0.3px;
  }

  .back-field {
    position: absolute;
    inset: 0;
    background: linear-gradient(160deg, var(--sky-light) 0%, var(--sky) 50%, var(--sky-deep) 100%);
  }
  .back-content {
    position: absolute;
    inset: 0;
    display: flex;
    flex-direction: column;
    align-items: center;
    justify-content: center;
    gap: 18px;
  }
  .back-brand {
    display: flex;
    align-items: center;
    gap: 14px;
  }
  .back-brand .brand-dot {
    border-radius: 50%;
    border: 4px solid var(--pale);
    width: 40px; height: 40px;
  }
  .back-brand .brand-name {
    font-weight: 800;
    font-size: 36px;
    letter-spacing: 5px;
    text-transform: uppercase;
    color: var(--pale);
  }
  .back-web {
    font-weight: 500;
    font-size: 15px;
    color: var(--pale);
    letter-spacing: 0.5px;
  }
</style>
</head>
<body>

  <section class="card card-front">
    <div class="front-brand">
      <span class="brand-dot"></span>
      <span class="brand-name">SkyvornQ</span>
    </div>

    <div class="divider"></div>

    <div class="contact">
      <p class="person-name">Dara Whitfield</p>
      <p class="person-title">CEO/Founder</p>
      <ul class="contact-list">
        <li>
          <svg viewBox="0 0 12 12"><rect x="3" y="0.5" width="6" height="11" rx="1.2" fill="none" stroke="#2f9fd8" stroke-width="1.3"/><circle cx="6" cy="9.5" r="0.7" fill="#2f9fd8"/></svg>
          555-214-0962
        </li>
        <li>
          <svg viewBox="0 0 12 12"><path d="M2.5 1 L4.5 1 L5.3 3.6 L4 4.6 C4.7 6 6 7.3 7.4 8 L8.4 6.7 L11 7.5 L11 9.5 C11 10.3 10.3 11 9.5 11 C5 10.6 1.4 7 1 2.5 C1 1.7 1.7 1 2.5 1 Z" fill="#2f9fd8"/></svg>
          555-214-0962
        </li>
        <li>
          <svg viewBox="0 0 12 12"><rect x="0.7" y="2.2" width="10.6" height="7.6" rx="0.8" fill="none" stroke="#2f9fd8" stroke-width="1.2"/><path d="M1 2.6 L6 6.6 L11 2.6" fill="none" stroke="#2f9fd8" stroke-width="1.2"/></svg>
          dara@skyvornq.com
        </li>
        <li>
          <svg viewBox="0 0 12 12"><circle cx="6" cy="6" r="5.2" fill="none" stroke="#2f9fd8" stroke-width="1.1"/><ellipse cx="6" cy="6" rx="2.2" ry="5.2" fill="none" stroke="#2f9fd8" stroke-width="1"/><line x1="0.8" y1="6" x2="11.2" y2="6" stroke="#2f9fd8" stroke-width="1"/></svg>
          www.skyvornq.com
        </li>
      </ul>
    </div>

    <p class="address">4827 Trellis Hollow Road, Fort Pierce, Florida, 34951</p>
  </section>

  <section class="card card-back">
    <div class="back-field" role="img" aria-label="Blue background with a faint repeating brand pattern"></div>
    <div class="back-content">
      <div class="back-brand">
        <span class="brand-dot"></span>
        <span class="brand-name">SkyvornQ</span>
      </div>
      <p class="back-web">www.skyvornq.com</p>
    </div>
  </section>

</body>
</html>
```